Print materials for 3-star hotel

We are changing up our print materials (notepads, letterheads, key card jackets, small flyer for the room rates) We are a 3 star business hotel in the Philippines and have mainly used grey tones and clean, simple lines. See attached photos for logo and hotel interior photos.

Target Market(s)

Business

Contact Information for Business Card

Corvale Terrace Hotel
Lindwell Banca Avenue corner Tolenta St Cebu City 6000 Philippines
Tel: +63 32 481 7302
Mobile: +63 917 648 2095
www.corvaleterracehotel.example

Font styles to use
Serif
Sans Serif

Requirements
Must have
• Simple
• Readable font and font size
Nice to have
• Neutral colors, grey and taupes
Should not have
• No purples and bright blues

```html
<!DOCTYPE html>
<html lang="en">
<head>
<meta charset="utf-8">
<title>Corvale Terrace Hotel — Business Card</title>
<link rel="stylesheet" href="https://fonts.googleapis.com/css2?family=Cormorant+Garamond:wght@500&family=Open+Sans:wght@400;700&display=swap">
<style>
  :root {
    --backdrop: #d9d4ce;
    --card: #141414;
    --card-edge: #1d1d1d;
    --silver: #b9b9b9;
    --silver-dim: #8a8a8a;
    --white: #f4f4f4;
    --rule: #6f6f6f;
  }
  * { box-sizing: border-box; margin: 0; padding: 0; }
  html, body {
    width: 1200px; height: 864px; overflow: hidden;
    background: var(--backdrop);
  }
  .sheet {
    position: relative; width: 1200px; height: 864px;
    display: flex; align-items: center; justify-content: center; gap: 56px;
  }
  .card {
    position: relative; width: 546px; height: 312px;
    background: linear-gradient(160deg, var(--card-edge), var(--card));
    border-radius: 3px;
    box-shadow: 0 14px 30px rgba(0,0,0,.28);
    color: var(--white);
  }
  .wordmark {
    font-family: "Cormorant Garamond", serif;
    font-weight: 500; text-transform: uppercase; text-align: center;
    letter-spacing: .22em; line-height: 1.25;
  }
  .wordmark .mark-square {
    display: block; margin: 0 auto 12px;
    width: 34px; height: 34px; background: currentColor;
  }

  /* Front */
  .card-front .wordmark {
    position: absolute; left: 0; right: 0; top: 92px;
    color: var(--silver); font-size: 20px;
  }
  .card-front .site {
    position: absolute; left: 0; right: 0; bottom: 46px; text-align: center;
    font-family: "Open Sans", sans-serif; font-size: 11px;
    letter-spacing: .2em; color: var(--silver-dim);
  }

  /* Back */
  .card-back .wordmark {
    position: absolute; left: 22px; width: 250px; top: 104px;
    color: var(--white); font-size: 17px;
  }
  .card-back .divider {
    position: absolute; left: 288px; top: 40px; bottom: 40px;
    width: 1px;
    background: linear-gradient(to bottom, transparent, var(--rule) 20%, var(--rule) 80%, transparent);
  }
  .contact {
    position: absolute; left: 304px; top: 46px; right: 12px;
    font-family: "Open Sans", sans-serif; font-size: 12px; line-height: 1.4;
  }
  .contact .name { font-weight: 700; font-size: 17px; line-height: 1.1; }
  .contact .role { text-transform: uppercase; font-size: 11.5px; margin-bottom: 6px; }
  .contact .address { margin-bottom: 5px; }
  .contact ul { list-style: none; }
  .contact li { display: flex; align-items: center; gap: 7px; white-space: nowrap; }
  .contact svg { width: 11px; height: 11px; flex: none; fill: var(--white); }
</style>
</head>
<body>
<main class="sheet">
  <section class="card card-front" aria-label="Card front">
    <div class="wordmark"><span class="mark-square"></span>Corvale Terrace<br>Hotel</div>
    <p class="site">www.corvaleterracehotel.example</p>
  </section>

  <section class="card card-back" aria-label="Card back">
    <div class="wordmark"><span class="mark-square"></span>Corvale Terrace<br>Hotel</div>
    <div class="divider"></div>
    <div class="contact">
      <p class="name">ELIAS MARREN</p>
      <p class="role">President</p>
      <p class="address">Lindwell Banca Avenue corner<br>Tolenta St, Cebu City 6000<br>Philippines</p>
      <ul>
        <li><svg viewBox="0 0 12 12"><path d="M1 4c0-2 2-3 5-3s5 1 5 3v1H8V4H4v1H1zM3 6h6l1 5H2z"/></svg>Tel: +63 32 481 7302</li>
        <li><svg viewBox="0 0 12 12"><path d="M3 0h6v12H3zM4 1.5v8h4v-8z"/></svg>Mobile: +63 917 648 2095</li>
        <li><svg viewBox="0 0 12 12"><path d="M0 2h12v8H0zm1 1v.5l5 3.5 5-3.5V3z"/></svg>elias@corvaleterrace.example</li>
        <li><svg viewBox="0 0 12 12"><path d="M6 0a6 6 0 1 0 0 12A6 6 0 0 0 6 0zm0 1.5a4.5 4.5 0 0 1 0 9 4.5 4.5 0 0 1 0-9zM5 3v4h3.5V6H6V3z"/></svg>www.corvaleterracehotel.example</li>
      </ul>
    </div>
  </section>
</main>
</body>
</html>
```